Marlow Sail Works President Business Card Carbon fiber catamarans

Hi.. I need a new business card design.. I am the President of a high tech yacht builder. We build Carbon Fiber go fast catamarans... Maybe we use the file I am sharing to you as the back of the card.. We need to look cool and crisp ...

Target Market(s)

Affluent People who will purchase a cool yacht

Industry/Entity Type

Custom Yacht Builder

Contact Information for Business Card

Dean Pellway , President, 731.508.2164 USA

Font styles to use
Serif

Requirements
Must have
• the clean crisp cool feel
Nice to have
• clean and crisp
Should not have
• Bold ugly

```html
<!DOCTYPE html>
<html lang="en">
<head>
<meta charset="utf-8">
<title>Marlow Sail Works — Business Card</title>
<link rel="stylesheet" href="https://fonts.googleapis.com/css2?family=Exo+2:wght@400;500&display=swap">
<style>
  :root {
    --backdrop: #1c1c1e;
    --carbon-dark: #141416;
    --carbon-mid: #2a2a2e;
    --panel-light: #4a4b50;
    --panel-dark: #1f2024;
    --silver: #d9dadd;
    --silver-soft: #b9bbc0;
    --text-light: #e6e7ea;
  }
  html, body {
    margin: 0;
    padding: 0;
    width: 1200px;
    height: 874px;
    overflow: hidden;
    background: var(--backdrop);
    font-family: "Exo 2", sans-serif;
  }
  .canvas {
    width: 1200px;
    height: 874px;
    display: flex;
    flex-direction: column;
    align-items: center;
    justify-content: center;
    gap: 56px;
  }
  .card {
    position: relative;
    width: 620px;
    height: 354px;
    overflow: hidden;
    box-shadow: 0 18px 40px rgba(0,0,0,0.55);
  }
  .card-front {
    background: radial-gradient(ellipse at 45% 40%, var(--carbon-mid), var(--carbon-dark) 75%);
  }
  .carbon-weave {
    position: absolute;
    inset: 0;
  }
  .wordmark {
    position: absolute;
    display: flex;
    align-items: center;
    gap: 14px;
    color: var(--silver);
    font-weight: 500;
    letter-spacing: 0.16em;
    text-transform: uppercase;
    white-space: nowrap;
  }
  .card-front .wordmark {
    left: 50%;
    top: 50%;
    transform: translate(-50%, -50%);
    font-size: 34px;
  }
  .wordmark-dot {
    width: 0.7em;
    height: 0.7em;
    border-radius: 50%;
    background: var(--silver);
    flex: none;
  }
  .card-back .shape-layer {
    position: absolute;
    inset: 0;
  }
  .card-back .wordmark {
    left: 336px;
    top: 150px;
    font-size: 17px;
    letter-spacing: 0.12em;
    gap: 9px;
  }
  .contact-block {
    position: absolute;
    left: 34px;
    top: 56px;
    color: var(--text-light);
  }
  .person-name {
    margin: 0;
    font-size: 22px;
    font-weight: 400;
    letter-spacing: 0.06em;
    text-transform: uppercase;
  }
  .person-title {
    margin: 2px 0 18px;
    font-size: 14px;
    color: var(--silver-soft);
  }
  .address {
    margin: 0 0 14px;
    font-size: 15px;
    line-height: 1.3;
    font-style: normal;
  }
  .contact-list {
    list-style: none;
    margin: 0;
    padding: 0;
    font-size: 15px;
    line-height: 1.55;
  }
  .contact-list li {
    display: flex;
    align-items: center;
    gap: 9px;
  }
  .contact-list svg {
    width: 13px;
    height: 13px;
    fill: var(--silver-soft);
    flex: none;
  }
</style>
</head>
<body>
<main class="canvas">

  <section class="card card-front" aria-label="Card front">
    <div class="carbon-weave" role="img" aria-label="Woven carbon fiber texture across the card face"></div>
    <div class="wordmark"><span class="wordmark-dot"></span>Marlow Sail Works</div>
  </section>

  <section class="card card-back" aria-label="Card back">
    <svg class="shape-layer" viewBox="0 0 620 354" width="620" height="354" aria-hidden="true">
      <defs>
        <linearGradient id="panelShade" x1="0" y1="0" x2="0" y2="1">
          <stop offset="0" stop-color="#54555a"/>
          <stop offset="1" stop-color="#1e1f23"/>
        </linearGradient>
        <radialGradient id="meshShade" cx="0.6" cy="0.4" r="0.7">
          <stop offset="0" stop-color="#2c2d31"/>
          <stop offset="1" stop-color="#111113"/>
        </radialGradient>
        <linearGradient id="bandShine" x1="0" y1="0" x2="0" y2="1">
          <stop offset="0" stop-color="#f0f1f3"/>
          <stop offset="0.6" stop-color="#a9abb0"/>
          <stop offset="1" stop-color="#6d6f74"/>
        </linearGradient>
      </defs>
      <rect width="620" height="354" fill="url(#panelShade)"/>
      <path d="M318,0 C300,140 330,270 448,354 L620,354 L620,0 Z" fill="url(#meshShade)" role="img" aria-label="Perforated metal texture on the right side"/>
      <path d="M310,0 C292,140 322,272 440,354" fill="none" stroke="url(#bandShine)" stroke-width="9"/>
    </svg>

    <div class="contact-block">
      <h1 class="person-name">Dean Pellway</h1>
      <p class="person-title">President</p>
      <address class="address">410 Harbor Reach Road<br>Newport<br>Rhode Island 02840</address>
      <ul class="contact-list">
        <li><svg viewBox="0 0 16 16"><path d="M3.6 1.5l2.3 2.9-1.4 1.6c.9 2 2.5 3.6 4.5 4.5l1.6-1.4 2.9 2.3-1.3 2.2C7 13.5 2.5 9 1.4 3z"/></svg>731.508.2164</li>
        <li><svg viewBox="0 0 16 16"><path d="M4.5 1h7v14h-7zM6 2.5v9h4v-9zM7.3 12.5h1.4v1.2H7.3z"/></svg>731.508.2977</li>
        <li><svg viewBox="0 0 16 16"><path d="M1 3.5h14v9H1zM2.5 4.8v.4L8 9l5.5-3.8v-.4z"/></svg>dean@marlowsail.com</li>
        <li><svg viewBox="0 0 16 16"><circle cx="8" cy="8" r="7"/></svg>www.marlowsail.com</li>
      </ul>
    </div>

    <div class="wordmark"><span class="wordmark-dot"></span>Marlow Sail Works</div>
  </section>

</main>
</body>
</html>
```